Drone service provider needs a brilliant web design

I need a responsive web design for a new drone service company. Pelham Drone Solutions provides turnkey solutions to capture, process, and deliver actionable aerial data to customers. The design should communicate a professional company that is safe, legal and insured. I included our logo design and business card designs for reference.
*content to be supplied after design selected

Target Market(s)

We serve telecommunications, construction, government, utility infrastructure, insurance and other industries.

Industry/Entity Type

Industrial

Number of Pages Required

5+ page

Colors

Designer to choose colors to be used in the design.

Requirements
Must have
• The design should highlight professional services to include Inspections, Mapping, Consulting and Training. The site should include aerial images and video to compliment the services offered. The landing page must include following sections in order: HOME, SERVICES, ABOUT, DEMO REEL, CLIENTS, CONTACT FORM, and social media buttons (Facebook, LinkedIn, Twitter, YouTube, Instagram). Contact: 615-382-9041 info@pelhamdronesolutions-example.com Smyrna, TN
• Sitemap:
• 6 pages: Home, Inspections, Mapping, Training, Consulting, About
• HOME (Landing Page)
• • Header with logo and tab links (Home, Services, About, Contact)
• • 'CAPTURE. PROCESS. DELIVER.' tagline and 'CONTACT US' button displayed within aerial image of drone over city or construction site
• • Services section with icons, text and read more link to page
• • About section with photo and text with three icons for SAFE. LEGAL. INSURED.
• • Demo reel
• • Clients logos shown scrolling horizontally
• • Contact form
• • Footer with logo, phone, email, social media buttons
• SERVICES (4 different pages)
• • Inspections
• • Mapping
• • Consulting
• • Training
• ABOUT page
• • Company
• • Partners
• • Certifications & Associations
• • Careers
• CONTACT linked to bottom of landing page
• Would you like to receive the newsletter? Yes or No Drop-down list
Nice to have
• Photos of KVR Marlin or Corvex inspecting infrastructure, buildings, construction sites, etc. A photo of one or two pilots in vest and helmet. Free stock photos preferred but would purchase the right photo that's more relevant.
• website references:
• https://www.quillrotor-example.com/
• https://www.brentfieldworks-example.com/services
• https://www.tomaro-example.com/
• http://gantrymetric-example.com/
• http://lumbrook-example.com/
• http://fennotics-example.com/
• https://www.grebe-example.io/
Should not have
• not an aerial photography or videography service business, no blog or newsletter

```html
<!DOCTYPE html>
<html lang="en">
<head>
<meta charset="utf-8">
<title>Pelham Drone Solutions</title>
<link href="https://fonts.googleapis.com/css2?family=Montserrat:wght@400;600;700;800&family=Open+Sans:wght@400;600;700&display=swap" rel="stylesheet">
<style>
:root{
  --blue:#1f8fd6;
  --blue-dark:#1677b8;
  --ink:#2a2a2a;
  --charcoal:#2d2d2d;
  --grey-text:#8a8a8a;
  --line:#d9d9d9;
  --white:#ffffff;
}
*{margin:0;padding:0;box-sizing:border-box}
html,body{width:1200px;height:3656px;overflow:hidden}
body{position:relative;background:var(--white);font-family:"Open Sans",Arial,sans-serif;color:var(--ink)}
.abs{position:absolute}

/* header */
.topbar{left:0;top:0;width:1200px;height:112px;background:var(--blue);z-index:3}
.nav{left:96px;top:44px;display:flex;gap:40px;z-index:4}
.nav a{color:var(--white);font:600 15px "Montserrat",sans-serif;text-decoration:none;letter-spacing:.5px}
.logo-tab{left:420px;top:0;z-index:4}
.brand{left:420px;top:0;width:360px;height:100px;display:flex;align-items:center;justify-content:center;z-index:5;
  font:800 26px "Montserrat",sans-serif;color:var(--ink);text-transform:uppercase;letter-spacing:1px}
.social{right:92px;top:38px;display:flex;gap:10px;z-index:4}
.social span{width:30px;height:30px;border:2px solid var(--white);border-radius:4px;display:block}

/* hero */
.hero-img{left:0;top:0;width:1200px;height:680px;
  background:linear-gradient(180deg,#9fb5c6 0%,#7d96ab 35%,#5e7a8f 60%,#7fa2b3 100%)}
.hero-title{left:100px;top:236px;color:var(--white);font:800 62px/64px "Montserrat",sans-serif;letter-spacing:1px;z-index:2}
.btn-contact{left:100px;top:442px;width:142px;height:46px;background:var(--white);border-radius:4px;
  color:var(--blue);font:600 15px "Open Sans",sans-serif;display:flex;align-items:center;justify-content:center;z-index:2}
.hero-arrows{left:100px;top:538px;z-index:2}
.hero-wave{left:0;top:560px;z-index:2}

/* services */
.section-title{width:1200px;left:0;text-align:center;color:var(--blue);font:700 28px "Montserrat",sans-serif;letter-spacing:.5px}
.title-rule{width:70px;height:3px;background:var(--blue);left:565px}
.services{left:100px;top:856px;width:1000px;display:flex;justify-content:space-between}
.service{width:220px;text-align:center}
.service-icon{width:100px;height:100px;border:4px solid var(--blue);border-radius:50%;margin:0 auto;display:flex;align-items:center;justify-content:center}
.service h3{margin-top:22px;font:700 17px "Montserrat",sans-serif;letter-spacing:2px;color:var(--ink)}
.service p{margin-top:10px;font:400 13px/19px "Open Sans",sans-serif;color:var(--grey-text)}
.service a{display:block;margin-top:20px;color:var(--blue);font:600 15px "Open Sans",sans-serif;text-decoration:none}

/* about */
.about-bg{left:0;top:1200px}
.about-photo{left:100px;top:1344px;width:460px;height:356px;background:linear-gradient(160deg,#c9d3db 0%,#9aa7b2 45%,#6e7a6a 75%,#b9c94a 100%)}
.about-title{left:608px;top:1350px;color:var(--white);font:700 32px "Montserrat",sans-serif}
.about-text{left:608px;top:1410px;width:490px;color:#cfcfcf;font:400 14px/22px "Open Sans",sans-serif}
.about-text p+p{margin-top:14px}
.pillars{left:608px;top:1580px;display:flex;gap:60px}
.pillar{width:72px;text-align:center;color:var(--white);font:700 17px "Montserrat",sans-serif;letter-spacing:1px}
.pillar svg{display:block;margin:0 auto 14px}

/* demo reel */
.reel{left:100px;top:1924px;width:996px;height:412px;border:6px solid #d3d3d3;
  background:linear-gradient(120deg,#6c8f4f 0%,#8aa85a 35%,#c7c060 55%,#5f8a45 100%)}
.reel-play{left:570px;top:2100px}
.divider{left:100px;top:2416px;width:1000px;height:2px;background:var(--line)}
.clients{left:100px;top:2476px;width:1000px;display:flex;justify-content:space-between}
.client{width:130px;height:94px;border:1px solid var(--line);display:flex;align-items:center;justify-content:center}
.client span{width:84px;height:26px;background:#bdbdbd;border-radius:3px;display:block}

/* contact */
.contact-bg{left:0;top:2620px;width:1200px;height:640px;background:linear-gradient(180deg,var(--blue) 0%,var(--blue-dark) 100%)}
.contact-title{left:0;top:2688px;width:1200px;text-align:center;color:var(--white);font:700 28px "Montserrat",sans-serif}
.contact-rule{left:565px;top:2740px;width:70px;height:3px;background:var(--white)}
.field{height:52px;border:2px solid rgba(255,255,255,.85);border-radius:4px;color:var(--white);
  font:400 14px "Open Sans",sans-serif;padding:0 14px;display:flex;align-items:center}
.field.msg{height:98px;align-items:flex-start;padding-top:14px}
.news-label{left:612px;top:2910px;color:var(--white);font:600 14px "Open Sans",sans-serif;height:52px;display:flex;align-items:center}
.news-select{left:930px;top:2910px;width:145px;justify-content:space-between}
.btn-submit{left:540px;top:3090px;width:120px;height:46px;background:var(--white);border-radius:4px;color:var(--blue);
  font:600 15px "Open Sans",sans-serif;display:flex;align-items:center;justify-content:center}
.contact-wave{left:0;top:3140px}

/* footer */
.footer-bg{left:0;top:3230px;width:1200px;height:426px;background:var(--charcoal)}
.footer-brand{left:0;top:3334px;width:1200px;text-align:center;color:var(--white);font:800 30px "Montserrat",sans-serif;text-transform:uppercase;letter-spacing:1px}
.footer-contacts{left:0;top:3452px;width:1200px;display:flex;justify-content:center;gap:60px;color:var(--white);font:400 16px "Open Sans",sans-serif}
.footer-contacts div{display:flex;align-items:center;gap:12px}
.footer-nav{left:0;top:3530px;width:1200px;display:flex;justify-content:center;gap:48px;color:var(--white);font:600 13px "Montserrat",sans-serif}
.footer-nav .sep{color:#888}
.footer-rule{left:100px;top:3580px;width:1000px;height:1px;background:#555}
.copyright{left:100px;top:3608px;color:#bdbdbd;font:400 12px "Open Sans",sans-serif}
</style>
</head>
<body>

<!-- HEADER -->
<div class="abs topbar"></div>
<nav class="abs nav"><a href="#">HOME</a><a href="#">SERVICES</a><a href="#">ABOUT</a></nav>
<svg class="abs logo-tab" width="360" height="112" viewBox="0 0 360 112"><path d="M0 0H360L320 100Q316 106 308 106H52Q44 106 40 100Z" fill="#fff"/></svg>
<div class="abs brand">Pelham Drone Solutions</div>
<div class="abs social" aria-label="Social media links"><span></span><span></span><span></span><span></span><span></span><span></span></div>

<!-- HERO -->
<div class="abs hero-img" role="img" aria-label="Aerial photo of a drone flying over a city construction site"></div>
<h1 class="abs hero-title">CAPTURE.<br>PROCESS.<br>DELIVER.</h1>
<div class="abs btn-contact">Contact Us</div>
<svg class="abs hero-arrows" width="80" height="30" viewBox="0 0 80 30"><path d="M22 6L10 15L22 24M10 15H34" stroke="#fff" stroke-width="3" fill="none"/><path d="M58 6L70 15L58 24M70 15H46" stroke="#fff" stroke-width="3" fill="none"/></svg>
<svg class="abs hero-wave" width="1200" height="130" viewBox="0 0 1200 130" preserveAspectRatio="none">
  <path d="M0 90Q600 150 1200 0V130H0Z" fill="var(--blue)"/>
  <path d="M0 104Q600 160 1200 22V130H0Z" fill="#fff"/>
</svg>

<!-- SERVICES -->
<h2 class="abs section-title" style="top:738px">OUR SERVICES</h2>
<div class="abs title-rule" style="top:790px"></div>
<div class="abs services">
  <div class="service">
    <div class="service-icon"><svg width="50" height="50" viewBox="0 0 50 50" fill="none" stroke="#1f8fd6" stroke-width="4"><circle cx="21" cy="21" r="13"/><path d="M31 31L44 44"/></svg></div>
    <h3>INSPECTIONS</h3>
    <p>Close visual checks of towers, roofs and bridges without scaffolds, lifts or downtime for crews.</p>
    <a href="#">Read More &gt;</a>
  </div>
  <div class="service">
    <div class="service-icon"><svg width="50" height="50" viewBox="0 0 50 50" fill="none" stroke="#1f8fd6" stroke-width="4" stroke-linejoin="round"><path d="M6 12L18 7L32 12L44 7V38L32 43L18 38L6 43Z"/><path d="M18 7V38M32 12V43"/></svg></div>
    <h3>MAPPING</h3>
    <p>Accurate orthomosaic maps and surface models for sites, surveys and progress tracking over time.</p>
    <a href="#">Read More &gt;</a>
  </div>
  <div class="service">
    <div class="service-icon"><svg width="50" height="50" viewBox="0 0 50 50" fill="none" stroke="#1f8fd6" stroke-width="4" stroke-linejoin="round"><rect x="5" y="8" width="28" height="20" rx="3"/><path d="M12 28V36L20 28"/><path d="M37 16H45V36H40V42L33 36H22V32"/></svg></div>
    <h3>CONSULTING</h3>
    <p>Guidance on building an in-house drone program, from equipment choice to flight policy.</p>
    <a href="#">Read More &gt;</a>
  </div>
  <div class="service">
    <div class="service-icon"><svg width="50" height="50" viewBox="0 0 50 50" fill="none" stroke="#1f8fd6" stroke-width="4" stroke-linejoin="round"><path d="M3 18L25 8L47 18L25 28Z"/><path d="M12 23V35Q25 43 38 35V23"/><path d="M44 20V32"/></svg></div>
    <h3>TRAINING</h3>
    <p>Hands-on courses that prepare your staff for licensing, safe flight and field data capture.</p>
    <a href="#">Read More &gt;</a>
  </div>
</div>

<!-- ABOUT -->
<svg class="abs about-bg" width="1200" height="660" viewBox="0 0 1200 660" preserveAspectRatio="none">
  <path d="M0 40Q600 -30 1200 40V600Q600 690 0 600Z" fill="var(--charcoal)"/>
</svg>
<div class="abs about-photo" role="img" aria-label="Photo of a drone pilot in safety vest and helmet flying a drone beside a building under construction"></div>
<h2 class="abs about-title">About Pelham Drone Solutions</h2>
<div class="abs about-text">
  <p>We capture, process and deliver actionable aerial data for telecommunications, construction, government, utility and insurance clients. Every mission is planned with care, flown by licensed pilots and backed by full coverage, so you get the answers you need without the risk.</p>
  <p>Based in Smyrna, Tennessee, our team supports projects across the region with fast turnaround and clear reporting.</p>
</div>
<div class="abs pillars">
  <div class="pillar"><svg width="46" height="52" viewBox="0 0 46 52" fill="none" stroke="#fff" stroke-width="4" stroke-linejoin="round"><path d="M23 3L42 10V24Q42 40 23 49Q4 40 4 24V10Z"/><path d="M14 25L21 32L33 19"/></svg>SAFE</div>
  <div class="pillar"><svg width="52" height="52" viewBox="0 0 52 52" fill="#fff"><rect x="14" y="6" width="24" height="12" rx="2" transform="rotate(-40 26 12)"/><rect x="22" y="16" width="6" height="30" rx="2" transform="rotate(-40 25 31)"/><rect x="4" y="44" width="26" height="6" rx="2"/></svg>LEGAL</div>
  <div class="pillar"><svg width="52" height="52" viewBox="0 0 52 52" fill="none" stroke="#fff" stroke-width="4" stroke-linejoin="round"><path d="M4 26Q26 -6 48 26Q42 21 37 26Q31 21 26 26Q21 21 15 26Q10 21 4 26Z" fill="#fff"/><path d="M26 26V42Q26 48 20 48Q16 48 15 44"/></svg>INSURED</div>
</div>

<!-- DEMO REEL -->
<div class="abs reel" role="img" aria-label="Demo reel video still: drone over green farm fields with a tablet showing crop mapping"></div>
<svg class="abs reel-play" width="60" height="60" viewBox="0 0 60 60"><circle cx="30" cy="30" r="26" fill="rgba(0,0,0,.35)" stroke="#fff" stroke-width="4"/><path d="M24 18L42 30L24 42Z" fill="#fff"/></svg>

<!-- CLIENTS -->
<div class="abs divider"></div>
<div class="abs clients" aria-label="Client logos">
  <div class="client"><span></span></div><div class="client"><span></span></div><div class="client"><span></span></div>
  <div class="client"><span></span></div><div class="client"><span></span></div><div class="client"><span></span></div>
</div>

<!-- CONTACT -->
<div class="abs contact-bg"></div>
<h2 class="abs contact-title">CONTACT FORM</h2>
<div class="abs contact-rule"></div>
<div class="abs field" style="left:125px;top:2822px;width:463px">Name</div>
<div class="abs field" style="left:612px;top:2822px;width:463px">Phone Number</div>
<div class="abs field" style="left:125px;top:2910px;width:463px">Email Address</div>
<div class="abs news-label">Would you like to receive the newsletter?</div>
<div class="abs field news-select">Yes <svg width="12" height="8" viewBox="0 0 12 8"><path d="M1 1L6 6L11 1" stroke="#fff" stroke-width="2" fill="none"/></svg></div>
<div class="abs field msg" style="left:125px;top:2966px;width:950px">Message</div>
<div class="abs btn-submit">Submit</div>
<svg class="abs contact-wave" width="1200" height="100" viewBox="0 0 1200 100" preserveAspectRatio="none">
  <path d="M0 30Q600 130 1200 10V100H0Z" fill="#fff"/>
  <path d="M0 50Q600 150 1200 40V100H0Z" fill="var(--charcoal)"/>
</svg>

<!-- FOOTER -->
<div class="abs footer-bg"></div>
<div class="abs footer-brand">Pelham Drone Solutions</div>
<div class="abs footer-contacts">
  <div><svg width="30" height="30" viewBox="0 0 30 30" fill="none" stroke="#fff" stroke-width="2"><circle cx="15" cy="15" r="13"/><rect x="8" y="10" width="14" height="10"/><path d="M8 10L15 16L22 10"/></svg>info@pelhamdronesolutions-example.com</div>
  <div><svg width="30" height="30" viewBox="0 0 30 30" fill="none" stroke="#fff" stroke-width="2"><circle cx="15" cy="15" r="13"/><path d="M10 8L13 8L14 12L12 13Q13 16 17 18L18 16L22 17V20Q22 22 20 22Q9 21 8 10Q8 8 10 8Z" fill="#fff"/></svg>615-382-9041</div>
</div>
<nav class="abs footer-nav"><span>HOME</span><span class="sep">|</span><span>SERVICES</span><span class="sep">|</span><span>ABOUT</span><span class="sep">|</span><span>CONTACT US</span></nav>
<div class="abs footer-rule"></div>
<div class="abs copyright">Copyright © 2018 Pelham Drone Solutions. All Right Reserved</div>

</body>
</html>
```